The Vellmark Cipher: A financial thriller fiction

cover, spine and reverse for Book 1 of the Gavin Shreve & Nadia Fenwick Harbors in Eclipse Series.

America is under attack.
Fueled by resentment of America's global dominance, Russia and China conspire to dethrone the US Dollar from its lofty perch as the global reserve currency. Their weapon of choice? Quindar — a game-changing digital currency shrouded in mystery, with an enigmatic developer who walked away from a 70-billion-dollar fortune rather than see his creation corrupted by evil.
Enter dazzling KDO operative Nadia Fenwick and Hearthrob FLEET Warden turned PVB Deputy Director Gavin Shreve. Amid an atmosphere of intrigue and danger, it falls to this duo to foil the grand scheme and rebuild a world ravaged by nuclear conflict. But their mission is complicated by an egocentric President who remains unconcerned with global fallout as long as his personal economic interests remain unaffected.
As they navigate a landscape reshaped by war, pandemic, and Quindar, will America rise to its historic role as a leader with a strong moral compass?
Or will a new world order ascend, driven by Russia, China, and the shadowy power of Quindar?

THE VELLMARK CIPHER delivers high-stakes drama, global politics, and tantalizing romance in a fast-paced thriller packed with adrenaline and nail-biting suspense!

Target Market(s)

mostly male readers of thriller fiction

Industry/Entity Type

fiction

Requirements
Must have
• symbols of Russia, China, Quindar and US currency. ALSO, a hero and heroine. seee images attached
Nice to have
• see attached covers. DO NOT duplicate the one titled "The Vellmark Cipher". It has the symbols I want but rejected as too cartoonish

```html
<!DOCTYPE html>
<html lang="en">
<head>
<meta charset="utf-8">
<title>The Vellmark Cipher – Book Wrap</title>
<link rel="stylesheet" href="https://fonts.googleapis.com/css2?family=Cinzel:wght@400;600;700&display=swap">
<style>
  :root{
    --ink:#06090c;
    --back-top:#0b1418;
    --panel:rgba(18,92,104,.55);
    --panel-edge:rgba(60,170,190,.35);
    --pill:#08a5e8;
    --pill-ink:#04121c;
    --glow:#9fe6ff;
    --white:#f4fbff;
    --red:#8e1a1e;
    --red-badge:#c9252b;
    --paper:#eeeae4;
    --art-deep:#0a3550;
    --art-mid:#1d7fae;
    --art-light:#5fc6ea;
    --gold:#d9a227;
  }
  *{margin:0;padding:0;box-sizing:border-box}
  html,body{width:1200px;height:803px;overflow:hidden;background:var(--ink)}
  body{font-family:"Cinzel",serif;color:var(--white)}
  .wrap{position:relative;width:1200px;height:803px;overflow:hidden}

  /* ---------- back cover ---------- */
  .back{position:absolute;left:0;top:0;width:553px;height:803px;
    background:radial-gradient(ellipse at 50% 45%,#10262c 0%,var(--back-top) 45%,var(--ink) 100%)}
  .glow-text{color:var(--white);text-shadow:0 0 6px var(--glow),0 0 14px rgba(90,200,255,.6)}
  .back-title{position:absolute;left:0;width:553px;top:30px;text-align:center;
    font-weight:700;font-size:45px;line-height:52px;letter-spacing:1px}
  .back-author{position:absolute;left:0;width:553px;top:143px;text-align:center;font-size:21px;font-weight:600}
  .panel{position:absolute;left:45px;width:479px;background:var(--panel);
    border-radius:26px;box-shadow:0 0 18px var(--panel-edge) inset,0 0 12px rgba(40,160,190,.25)}
  .panel-book{top:190px;height:215px}
  .panel-author{top:444px;height:218px}
  .pill{position:absolute;left:174px;width:211px;height:30px;background:var(--pill);
    border-radius:8px;color:var(--pill-ink);font-weight:600;font-size:16px;
    display:flex;align-items:center;justify-content:center}
  .pill-book{top:186px}
  .pill-author{top:435px}
  .blurb{position:absolute;left:60px;width:449px;top:228px;text-align:center;
    font-size:7.6px;line-height:10.4px;font-weight:600;text-transform:uppercase}
  .blurb p+p{margin-top:10px}
  .author-photo{position:absolute;left:87px;top:485px;width:96px;height:97px;border-radius:8px;
    border:2px solid #d8c86a;background:linear-gradient(160deg,#6c7a6a,#b7a795 60%,#8d9aa6)}
  .author-bio{position:absolute;left:200px;top:488px;width:310px;font-size:7.8px;line-height:11.2px;
    font-weight:600;text-transform:uppercase}
  .author-bio .name{font-size:16px}
  .author-more{position:absolute;left:80px;top:596px;width:400px;text-align:center;
    font-size:7.8px;line-height:11px;font-weight:600;text-transform:uppercase}

  /* ---------- spine ---------- */
  .spine{position:absolute;left:553px;top:0;width:95px;height:803px;background:#030507}
  .spine-author{position:absolute;left:601px;top:164px;transform:translate(-50%,-50%) rotate(90deg);
    white-space:nowrap;font-size:21px;font-weight:600}
  .spine-title{position:absolute;left:604px;top:596px;transform:translate(-50%,-50%) rotate(-90deg);
    white-space:nowrap;font-size:28px;line-height:31px;font-weight:700;text-align:left}

  /* ---------- front cover ---------- */
  .front{position:absolute;left:648px;top:0;width:552px;height:803px;overflow:hidden}
  .front-art{position:absolute;inset:0;
    background:radial-gradient(ellipse at 55% 42%,var(--art-light) 0%,var(--art-mid) 32%,var(--art-deep) 70%,#071a2a 100%)}
  .figures{position:absolute;left:110px;top:265px;width:300px;height:420px;
    background:linear-gradient(180deg,rgba(10,18,28,.85),rgba(10,22,36,.55) 70%,rgba(10,22,36,0))}
  .emblem{position:absolute;left:125px;top:482px;width:170px;height:170px;border-radius:50%;
    background:radial-gradient(circle,#e24a3a,#b8201f 70%,#d9d9d9 72%)}
  .coin{position:absolute;left:277px;top:477px;width:170px;height:180px;border-radius:50%;
    background:radial-gradient(circle at 45% 40%,#f3cf63,var(--gold) 55%,#9d6c14)}
  .chart{position:absolute;left:0;top:420px}
  .red-band{position:absolute;left:0;top:0;width:552px;height:215px;
    background:linear-gradient(90deg,#6f1518,var(--red) 40%,#7a1a1d)}
  .front-title{position:absolute;left:0;width:552px;top:52px;text-align:center;
    font-weight:700;font-size:48px;line-height:58px;letter-spacing:1px}
  .tear{position:absolute;left:0;top:170px}
  .series-line{position:absolute;top:212px;font-size:13px;font-weight:600;color:#2a1a18;
    transform:rotate(-3deg);white-space:nowrap}
  .heroes{left:12px;top:218px}
  .series{left:340px;top:207px}
  .book-no{position:absolute;left:214px;top:176px;width:106px;height:72px;display:flex;
    align-items:center;justify-content:center;font-size:52px;font-weight:700;color:var(--white);
    text-shadow:0 0 4px rgba(255,255,255,.6)}
  .front-author{position:absolute;left:0;width:552px;top:733px;text-align:center;
    font-size:40px;font-weight:600;letter-spacing:1px}
</style>
</head>
<body>
<div class="wrap">

  <section class="back">
    <h1 class="back-title glow-text">THE VELLMARK<br>CIPHER</h1>
    <p class="back-author glow-text">-REID HARLOW</p>

    <div class="panel panel-book"></div>
    <div class="pill pill-book">About the Book</div>
    <div class="blurb glow-text">
      <p>In a world rife with clandestine machinations and veiled intentions, a sinister alliance between Russia and China threatens to shatter the very foundations of the global order. Fueled by decades of resentment toward America's dominance, the deadly duo conspires to unleash chaos, using the Covid pandemic and the invasion of Ukraine as weapons in their master plan.</p>
      <p>Add in the enigmatic world of cryptocurrencies, where the shadowy creator of Quindar, Oren Vask, holds the key to a groundbreaking financial upheaval. As the US dollar teeters precariously, the true intentions of the plot become clear.</p>
      <p>"The Vellmark Cipher" immerses you in an exhilarating geopolitical thriller, revealing the treacherous side of international politics and the relentless pursuit of power. Explore a high-stakes game where trust is a luxury, and the fate of the world hangs in the balance.</p>
    </div>

    <div class="panel panel-author"></div>
    <div class="pill pill-author">About the Author</div>
    <div class="author-photo" role="img" aria-label="Author portrait photograph"></div>
    <p class="author-bio glow-text"><span class="name">Reid Harlow</span>, author of "The Vellmark Cipher," has been navigating the intricate world of finance for over 43 years, amassing a wealth of knowledge and experience. As an early adopter of Quindar and an insatiable student of world history and finance, Reid weaves his expertise into thrilling narratives that keep readers on the edge of their seats.</p>
    <p class="author-more glow-text">When he's not spinning tales of intrigue, Reid volunteers as CEO of a non-profit he co-founded and plotting his next groundbreaking financial move. Join him for an electrifying journey into the cryptic world of cryptocurrencies and global power plays.</p>
  </section>

  <section class="spine">
  </section>
  <p class="spine-author glow-text">-REID HARLOW</p>
  <p class="spine-title glow-text">THE VELLMARK<br>CIPHER</p>

  <section class="front">
    <div class="front-art" role="img" aria-label="Blue digital backdrop of binary code and a glowing coin motif"></div>
    <div class="figures" role="img" aria-label="Silhouettes of the hero and heroine standing side by side"></div>
    <svg class="chart" width="552" height="380" viewBox="0 0 552 380" aria-hidden="true">
      <polyline points="20,270 60,240 90,255 130,215 170,240 210,200 250,210 290,150 330,165 370,110 410,95 450,60 490,50 552,20"
        fill="none" stroke="#8fe3ff" stroke-width="2" opacity=".85"/>
      <polyline points="0,250 120,200 260,130 400,70 552,15" fill="none" stroke="#bdf0ff" stroke-width="1.2" opacity=".6"/>
    </svg>
    <div class="emblem" role="img" aria-label="Coin combining Russian and Chinese state emblems"></div>
    <div class="coin" role="img" aria-label="Gold Quindar digital coin"></div>

    <div class="red-band" role="img" aria-label="Red torn-paper banner with faint figures"></div>
    <h2 class="front-title glow-text">THE VELLMARK<br>CIPHER</h2>
    <svg class="tear" width="552" height="100" viewBox="0 0 552 100" aria-hidden="true">
      <polygon points="0,40 120,30 210,22 330,18 440,12 552,8 552,60 440,66 330,76 210,82 120,88 0,96" fill="var(--paper)"/>
      <polygon points="214,20 312,16 322,34 320,74 312,78 214,82 204,64 206,30" fill="var(--red-badge)"/>
    </svg>
    <div class="book-no">1</div>
    <p class="series-line heroes">Gavin Shreve &amp; Nadia Fenwick</p>
    <p class="series-line series">Harbors in Eclipse Series.</p>

    <p class="front-author glow-text">REID HARLOW</p>
  </section>

</div>
</body>
</html>
```